Bookcover: Ways to Turn Into a Bold Pathfinder

I am publishing a super-low-cost innovation book for €4,99 on Quillmere Open Press to help everyone become a great innovator: young ambitious people without college education nor a big budget. Do you want to help me?

Brief:
Design a book cover 1600 x 2560 pixels for QOP.
Main title: Ways to Turn Into a Bold Pathfinder
Sub title: mindset - insights - skills & tools
Author: Joost ter Brakel
Design: captive, and appealing to everyone
Target Group: young ambitious people without college education

For quillmere please format the height/width ratio of 1.6:1

```html
<!DOCTYPE html>
<html lang="en">
<head>
<meta charset="utf-8">
<title>Ways to Turn Into a Bold Pathfinder — Joost ter Brakel</title>
<link rel="stylesheet" href="https://fonts.googleapis.com/css2?family=Archivo:ital,wdth,wght@0,100,600;0,125,700;1,100,500&display=swap">
<style>
  :root {
    --cover-yellow: #FBBD2C;
    --ink: #1B1A17;
    --band-fill: #FCC43E;
    --art-tone-light: #E8B13A;
    --art-tone-deep: #C0922A;
    --mark-amber: #F0A21E;
  }
  html, body {
    margin: 0;
    padding: 0;
    width: 750px;
    height: 1200px;
    overflow: hidden;
    background: var(--cover-yellow);
  }
  .cover {
    position: relative;
    width: 750px;
    height: 1200px;
    background: var(--cover-yellow);
    overflow: hidden;
  }
  .title-art {
    position: absolute;
    left: 0;
    top: 0;
    width: 750px;
    height: 1200px;
  }
  .word-band {
    fill: var(--band-fill);
    stroke: var(--ink);
    stroke-width: 6;
    stroke-linejoin: round;
  }
  .word-rule {
    stroke: var(--ink);
    stroke-width: 3;
  }
  .block-word {
    font-family: "Archivo", Arial, sans-serif;
    font-stretch: 125%;
    font-weight: 700;
    fill: var(--ink);
  }
  .subtitle {
    font-family: "Archivo", Arial, sans-serif;
    font-style: italic;
    font-weight: 500;
    font-size: 23px;
    fill: var(--ink);
  }
  .author-line {
    position: absolute;
    left: 0;
    top: 1134px;
    width: 750px;
    margin: 0;
    display: flex;
    justify-content: center;
    align-items: center;
    gap: 10px;
    font-family: "Archivo", Arial, sans-serif;
    font-stretch: 100%;
    font-weight: 600;
    font-size: 25px;
    color: var(--ink);
  }
  .author-dot {
    width: 18px;
    height: 18px;
    border-radius: 50%;
    background: var(--mark-amber);
  }
</style>
</head>
<body>
<main class="cover">
  <svg class="title-art" viewBox="0 0 750 1200" width="750" height="1200" aria-labelledby="book-title">
    <title id="book-title">Ways to Turn Into a Bold Pathfinder</title>

    <g class="word-block" transform="translate(80,310)">
      <polygon class="word-band" points="0,0 149.8,-86.5 252,-27.5 102.2,59"/>
      <g transform="matrix(0.866,-0.5,0.866,0.5,0,0)">
        <text class="block-word" x="20" y="76" font-size="50" textLength="140" lengthAdjust="spacingAndGlyphs">WAYS</text>
      </g>
    </g>

    <g class="word-block" transform="translate(265,395)">
      <polygon class="word-band" points="0,0 324.8,-187.5 427,-128.5 102.2,59"/>
      <g transform="matrix(0.866,-0.5,0.866,0.5,0,0)">
        <text class="block-word" x="55" y="78" font-size="50" textLength="320" lengthAdjust="spacingAndGlyphs">TURN INTO</text>
      </g>
    </g>

    <g class="word-block" transform="translate(57,510)">
      <polygon class="word-band" points="0,0 149.8,-86.5 252,-27.5 102.2,59"/>
      <g transform="matrix(0.866,-0.5,0.866,0.5,0,0)">
        <text class="block-word" x="42" y="80" font-size="56">TO</text>
      </g>
    </g>

    <g class="word-block" transform="translate(250,595)">
      <polygon class="word-band" points="0,0 324.8,-187.5 427,-128.5 102.2,59"/>
      <g transform="matrix(0.866,-0.5,0.866,0.5,0,0)">
        <text class="block-word" x="80" y="80" font-size="54" textLength="270" lengthAdjust="spacingAndGlyphs">A BOLD</text>
      </g>
    </g>

    <defs>
      <linearGradient id="art-tone" x1="0" y1="0" x2="0" y2="1">
        <stop offset="0" stop-color="var(--art-tone-light)"/>
        <stop offset="1" stop-color="var(--art-tone-deep)"/>
      </linearGradient>
    </defs>
    <rect class="art-area" x="108" y="632" width="146" height="120" rx="60"
          fill="url(#art-tone)" opacity="0.55"
          role="img" aria-label="Illustration of a small stack of discs with a highlighted slice"/>

    <g class="word-block" transform="translate(187,802)">
      <polygon class="word-band" points="0,0 407,-235 509.2,-176 102.2,59"/>
      <g transform="matrix(0.866,-0.5,0.866,0.5,0,0)">
        <text class="block-word" x="30" y="81" font-size="54" textLength="430" lengthAdjust="spacingAndGlyphs">PATHFINDER</text>
      </g>
    </g>

    <text class="subtitle" transform="translate(350,902) rotate(-30)">mindset - insights - skills &amp; tools</text>
  </svg>

  <p class="author-line"><span class="author-dot" aria-hidden="true"></span>Joost ter Brakel</p>
</main>
</body>
</html>
```